Trading Company needs a business card design, letter head design and email signature

We need a double-sided business card design, letter head design and an email signature. We have a logo design.

Possible Tag Lines:
• “Connecting Worlds, Building Excellence.”
• “Trusted Trade, Quality Delivered.”
• “Bridging Borders, Building Quality.”
• “Worldwide Partnerships, Superior Goods.”
• “Where Quality Meets Affordability”

Services Offered:
Procurement
Fabrication
Distribution
Logistics
Import/Export

Requirements
Must have
• Nice quality double sided Business Card design, Letterhead design needs to be A4
Nice to have
• possible ideas on tag lines

```html
<!DOCTYPE html>
<html lang="en">
<head>
<meta charset="utf-8">
<title>Corvane Stationery</title>
<link href="https://fonts.googleapis.com/css2?family=Open+Sans:wght@400;600&family=Roboto:wght@400;500;700&display=swap" rel="stylesheet">
<style>
:root{
  --bg:#e6e7e9;
  --red:#e52421;
  --grey:#5d5f61;
  --ink:#3c3c3c;
  --muted:#6a6a6a;
  --black:#050505;
  --white:#ffffff;
}
*{margin:0;padding:0;box-sizing:border-box}
html,body{width:1200px;height:1087px;overflow:hidden;background:var(--bg);font-family:"Roboto",sans-serif;color:var(--ink)}
.canvas{position:relative;width:1200px;height:1087px}
.sheet{position:absolute;background:var(--white);box-shadow:2px 3px 6px rgba(0,0,0,.22);overflow:hidden}
.abs{position:absolute}
.brand{display:flex;align-items:center;gap:6px;font-weight:700;color:var(--red);letter-spacing:1px;white-space:nowrap}
.brand .mark{width:12px;height:12px;background:var(--red)}
.tagline{font-size:5px;font-weight:700;color:var(--red);letter-spacing:.4px;text-transform:uppercase;white-space:nowrap}
.band{position:absolute;left:0;bottom:0;width:100%}
.icon{display:inline-block;vertical-align:-1px;margin-right:4px}

/* letterhead */
.letterhead{left:101px;top:196px;width:491px;height:694px}
.letterhead .logo{left:0;width:100%;top:84px;display:flex;flex-direction:column;align-items:center;gap:3px}
.letterhead .brand{font-size:21px}
.letter-body{left:49px;top:164px;width:395px;font-family:"Open Sans",sans-serif;font-size:7.9px;line-height:13.1px;color:var(--muted)}
.letter-body p{margin-bottom:13.1px}
.signature{left:49px;top:508px;width:58px;height:52px;background:linear-gradient(135deg,#e9ecf3,#d3d9e6);border-radius:4px}
.letter-foot{left:0;width:100%;top:635px;text-align:center;font-size:11px;color:var(--muted);line-height:15.5px}
.letter-foot .row span{margin:0 3px}

/* card front */
.card-front{left:647px;top:196px;width:379px;height:216px;background:var(--black);border-radius:8px}
.card-front .logo{left:46px;top:120px;display:flex;flex-direction:column;align-items:center;gap:3px}
.card-front .brand{font-size:21px}
.divider{position:absolute;width:1px;background:#8a8a8a}
.services{left:200px;top:60px;color:#f2f2f2}
.services h2{font-size:10px;font-weight:700;color:var(--red);letter-spacing:.6px;margin-bottom:2px}
.services li{list-style:none;font-size:12.2px;line-height:15px}
.services li::before{content:"";display:inline-block;width:4px;height:4px;border-radius:50%;background:var(--red);margin-right:3px;vertical-align:2px}

/* card back */
.card-back{left:647px;top:434px;width:379px;height:215px;border-radius:8px}
.card-back .logo{left:48px;top:121px;display:flex;flex-direction:column;align-items:center;gap:3px}
.card-back .brand{font-size:21px}
.contact{left:207px;top:51px;font-size:11.2px;line-height:14.3px;color:var(--ink)}
.contact .name{font-size:12.4px;font-weight:700;color:#2b2b2b}
.contact .name b{color:var(--red)}
.contact .gap{height:10px}

/* email signature */
.email-sig{left:647px;top:702px;width:452px;height:159px}
.photo{left:30px;top:0;margin-top:30px;width:96px;height:96px;border-radius:50%;background:radial-gradient(circle at 50% 40%,#c9ccd2,#8e949d)}
.sig-text{left:161px;top:34px;font-size:9px;line-height:12.2px;color:var(--muted)}
.sig-text .name{font-size:10.6px;font-weight:700;color:#2b2b2b}
.sig-text .name b{color:var(--red)}
.sig-text .gap{height:6px}
.email-sig .logo{left:290px;top:80px;width:150px;display:flex;flex-direction:column;align-items:center;gap:3px}
.email-sig .brand{font-size:18px}
.socials{display:flex;gap:3px;margin-top:6px}
.socials span{width:11px;height:11px;border-radius:2px;background:#3f6fb3}
.socials span:last-child{background:var(--red)}
</style>
</head>
<body>
<div class="canvas">

  <!-- Letterhead -->
  <section class="sheet letterhead">
    <div class="abs logo">
      <div class="brand"><span class="mark"></span>CORVANE</div>
      <div class="tagline">Trusted Trade, Quality Delivered</div>
    </div>
    <div class="abs letter-body">
      <p>Dear customer,</p>
      <p>Lorem ipsum dolor sit amet, consectetur adipisicing elit, sed do eiusmod tempor incididunt ut labore et dolore magna aliqua. Ut enim ad minim veniam, quis nostrud exercitation ullamco laboris nisi ut aliquip ex ea commodo consequat. Duis aute irure dolor in reprehenderit in voluptate velit esse cillum dolore eu fugiat nulla pariatur. Excepteur sint occaecat cupidatat non proident, sunt in culpa qui officia deserunt mollit anim id est laborum.</p>
      <p>Lorem ipsum dolor sit amet, consectetur adipisicing elit, sed do eiusmod tempor incididunt ut labore et dolore magna aliqua. Ut enim ad minim veniam, quis nostrud exercitation ullamco laboris nisi ut aliquip ex ea commodo consequat. Duis aute irure dolor in reprehenderit in voluptate velit esse cillum dolore eu fugiat nulla pariatur. Excepteur sint occaecat cupidatat non proident, sunt in culpa qui officia deserunt mollit anim id est laborum.</p>
      <p>Lorem ipsum dolor sit amet, consectetur adipisicing elit, sed do eiusmod tempor incididunt ut labore et dolore magna aliqua. Ut enim ad minim veniam, quis nostrud exercitation ullamco laboris nisi ut aliquip ex ea commodo consequat. Duis aute irure dolor in reprehenderit in voluptate velit esse cillum dolore eu fugiat nulla pariatur. Excepteur sint occaecat cupidatat non proident, sunt in culpa qui officia deserunt mollit anim id est laborum.</p>
      <p>Lorem ipsum dolor sit amet, consectetur adipisicing elit, sed do eiusmod tempor incididunt ut labore et dolore magna aliqua. Ut enim ad minim veniam, quis nostrud exercitation ullamco laboris nisi ut aliquip ex ea commodo consequat. Duis aute irure dolor in reprehenderit.</p>
      <p>Yours Sincerely,</p>
    </div>
    <div class="abs signature" role="img" aria-label="Handwritten signature"></div>
    <div class="abs letter-foot">
      <div>48 Harbor Lane Suite 3 Salem, MA 01970</div>
      <div class="row">
        <span><svg class="icon" width="9" height="9" viewBox="0 0 10 10"><path d="M2 0.5l2 2-1 1.3c.6 1.3 1.6 2.3 2.9 2.9l1.3-1 2 2-1.3 1.8C4.3 9.2.8 5.7.5 1.8z" fill="var(--red)"/></svg>(555) 014-2290</span>
        <span><svg class="icon" width="10" height="8" viewBox="0 0 10 8"><rect x=".5" y=".5" width="9" height="7" fill="none" stroke="var(--red)"/><path d="M.5 .5l4.5 4 4.5-4" fill="none" stroke="var(--red)"/></svg>hello@corvanemail.com</span>
        <span><svg class="icon" width="9" height="9" viewBox="0 0 10 10"><circle cx="5" cy="5" r="4.3" fill="none" stroke="var(--red)"/><ellipse cx="5" cy="5" rx="2" ry="4.3" fill="none" stroke="var(--red)"/><path d="M.7 5h8.6" stroke="var(--red)"/></svg>www.corvaneweb.com</span>
      </div>
    </div>
    <svg class="band" height="11" viewBox="0 0 491 11" preserveAspectRatio="none"><rect width="491" height="11" fill="var(--grey)"/><polygon points="0,0 258,0 250,11 0,11" fill="var(--red)"/><polygon points="258,0 261,0 253,11 250,11" fill="var(--white)"/></svg>
  </section>

  <!-- Business card front -->
  <section class="sheet card-front">
    <div class="abs logo">
      <div class="brand"><span class="mark"></span>CORVANE</div>
      <div class="tagline">Trusted Trade, Quality Delivered</div>
    </div>
    <div class="divider" style="left:188px;top:64px;height:88px"></div>
    <div class="abs services">
      <h2>SERVICES OFFERED:</h2>
      <ul>
        <li>Procurement</li>
        <li>Fabrication</li>
        <li>Distribution</li>
        <li>Logistics</li>
        <li>Import/Export</li>
      </ul>
    </div>
  </section>

  <!-- Business card back -->
  <section class="sheet card-back">
    <div class="abs logo">
      <div class="brand"><span class="mark"></span>CORVANE</div>
      <div class="tagline">Trusted Trade, Quality Delivered</div>
    </div>
    <div class="divider" style="left:194px;top:51px;height:112px"></div>
    <div class="abs contact">
      <div class="name"><b>DANA</b> WHITLOCK</div>
      <div>Founder &amp; CEO</div>
      <div class="gap"></div>
      <div>48 Harbor Lane Suite</div>
      <div>3 Salem, MA 01970</div>
      <div style="height:5px"></div>
      <div><svg class="icon" width="10" height="10" viewBox="0 0 10 10"><path d="M2 0.5l2 2-1 1.3c.6 1.3 1.6 2.3 2.9 2.9l1.3-1 2 2-1.3 1.8C4.3 9.2.8 5.7.5 1.8z" fill="var(--red)"/></svg>(555) 014-2290</div>
      <div><svg class="icon" width="11" height="9" viewBox="0 0 10 8"><rect x=".5" y=".5" width="9" height="7" fill="none" stroke="var(--red)"/><path d="M.5 .5l4.5 4 4.5-4" fill="none" stroke="var(--red)"/></svg>hello@corvanemail.com</div>
      <div><svg class="icon" width="10" height="10" viewBox="0 0 10 10"><circle cx="5" cy="5" r="4.3" fill="none" stroke="var(--red)"/><ellipse cx="5" cy="5" rx="2" ry="4.3" fill="none" stroke="var(--red)"/><path d="M.7 5h8.6" stroke="var(--red)"/></svg>www.corvaneweb.com</div>
    </div>
    <svg class="band" height="11" viewBox="0 0 379 11" preserveAspectRatio="none"><rect width="379" height="11" fill="var(--grey)"/><polygon points="0,0 200,0 195,11 0,11" fill="var(--red)"/><polygon points="200,0 203,0 198,11 195,11" fill="var(--white)"/></svg>
  </section>

  <!-- Email signature -->
  <section class="sheet email-sig">
    <div class="abs photo" role="img" aria-label="Portrait photo of the managing director"></div>
    <div class="divider" style="left:144px;top:22px;height:116px"></div>
    <div class="abs sig-text">
      <div class="name"><b>TOBIAS R.</b> LINDQVIST, ESQ.</div>
      <div>Managing Director</div>
      <div class="gap"></div>
      <div>7 Maple Ridge Road,</div>
      <div>Aurora, ON L4G 0A1</div>
      <div class="gap"></div>
      <div><svg class="icon" width="8" height="8" viewBox="0 0 10 10"><path d="M2 0.5l2 2-1 1.3c.6 1.3 1.6 2.3 2.9 2.9l1.3-1 2 2-1.3 1.8C4.3 9.2.8 5.7.5 1.8z" fill="var(--red)"/></svg>(555) 019-4472</div>
      <div><svg class="icon" width="8" height="7" viewBox="0 0 10 8"><rect width="10" height="8" fill="var(--red)"/></svg>tobias@corvanemail.com</div>
      <div><svg class="icon" width="8" height="8" viewBox="0 0 10 10"><circle cx="5" cy="5" r="5" fill="var(--red)"/></svg>tobias@corvanemail.com</div>
    </div>
    <div class="abs logo">
      <div class="brand"><span class="mark"></span>CORVANE</div>
      <div class="tagline">Trusted Trade, Quality Delivered</div>
      <div class="socials"><span></span><span></span><span></span><span></span></div>
    </div>
    <svg class="band" height="7" viewBox="0 0 452 7" preserveAspectRatio="none"><rect width="452" height="7" fill="var(--grey)"/><polygon points="0,0 300,0 297,7 0,7" fill="var(--red)"/><polygon points="300,0 302,0 299,7 297,7" fill="var(--white)"/></svg>
  </section>

</div>
</body>
</html>
```